Looking for a modern, Professional business card design

We have a simple business card, but are looking for a more modern, professional look. A sample of the basic card is attached as well as the logo. We would also like to add that we offer:
Struggling with your finances?
- Learn to become debt free
- Discover the power of cash
- Control your money instead of it controlling you
Let us help you achieve a new level of financial freedom!
Also, we would like to have a "SPECIAL OFFER!: FREE 30 minute consultation"
Financial Planning

```html
<!DOCTYPE html>
<html lang="en">
<head>
<meta charset="utf-8">
<title>Clearpath Money Coaching – Business Card</title>
<link rel="stylesheet" href="https://fonts.googleapis.com/css2?family=Source+Sans+3:ital,wght@0,400;0,600;0,700;1,400&display=swap">
<style>
  :root {
    --stage: #161616;
    --card: #ffffff;
    --ink: #1f1f1f;
    --ink-soft: #3a3a3a;
    --green-dark: #2f6e1e;
    --green: #3f8f24;
    --green-light: #8cc63e;
  }
  * { margin: 0; padding: 0; box-sizing: border-box; }
  html, body { width: 1200px; height: 900px; overflow: hidden; }
  body {
    background: var(--stage);
    font-family: "Source Sans 3", Arial, sans-serif;
    color: var(--ink);
    position: relative;
  }
  .card {
    position: absolute;
    top: 306px;
    width: 440px;
    height: 271px;
    background: var(--card);
    border-radius: 10px;
  }
  .card--front { left: 149px; }
  .card--back { left: 608px; text-align: center; }

  /* front */
  .brand-mark {
    position: absolute;
    left: 38px; top: 104px;
    display: flex; align-items: center; gap: 8px;
    font-weight: 700; font-size: 19px; color: var(--green);
    letter-spacing: 0.3px;
  }
  .brand-mark__dot {
    width: 18px; height: 18px; border-radius: 50%;
    background: var(--green-light);
  }
  .contact { position: absolute; left: 199px; top: 84px; }
  .contact__name { font-size: 15.5px; font-weight: 600; color: var(--ink-soft); line-height: 19px; }
  .contact__name .first { color: var(--green-light); }
  .contact__role { font-size: 12.5px; color: var(--ink-soft); line-height: 15px; }
  .contact__list { list-style: none; margin-top: 18px; }
  .contact__item {
    display: flex; align-items: center; gap: 7px;
    font-size: 12.5px; line-height: 16px; color: var(--ink-soft);
  }
  .contact__icon { width: 9px; height: 9px; fill: var(--green); flex: none; }

  /* back */
  .brand-lockup {
    margin-top: 44px;
    display: inline-flex; align-items: center; gap: 9px;
    font-weight: 700; font-size: 24px; color: var(--ink);
    letter-spacing: 0.5px;
  }
  .brand-lockup__dot {
    width: 22px; height: 22px; border-radius: 50%;
    background: var(--green-light);
  }
  .pitch__title {
    margin-top: 36px;
    font-size: 13.5px; font-weight: 700; color: var(--green-dark);
    letter-spacing: 0.2px;
  }
  .pitch__list { list-style: none; margin-top: 4px; }
  .pitch__list li { font-size: 12.5px; line-height: 16px; color: var(--ink); }
  .pitch__promise {
    margin-top: 17px;
    font-size: 12px; font-style: italic; color: var(--green);
  }
  .offer {
    margin-top: 14px;
    font-size: 15px; font-weight: 700; color: var(--ink);
  }
  .offer__label { color: var(--green-dark); }
</style>
</head>
<body>
  <section class="card card--front">
    <div class="brand-mark"><span class="brand-mark__dot"></span>Clearpath</div>
    <div class="contact">
      <p class="contact__name"><span class="first">Daniel</span> R. Hayes</p>
      <p class="contact__role">Personal financial coach</p>
      <ul class="contact__list">
        <li class="contact__item">
          <svg class="contact__icon" viewBox="0 0 10 10"><path d="M2 0.5 L3.6 2.6 L2.8 3.6 Q4 5.9 6.4 7.2 L7.4 6.4 L9.5 8 L8.4 9.5 Q3.5 9 0.5 1.6 Z"/></svg>
          (205) 555-0182
        </li>
        <li class="contact__item">
          <svg class="contact__icon" viewBox="0 0 10 10"><rect x="0.5" y="2" width="9" height="6.5"/><path d="M0.5 2 L5 5.6 L9.5 2" fill="none" stroke="#fff" stroke-width="0.9"/></svg>
          daniel@steadyledgercoaching.com
        </li>
        <li class="contact__item">
          <svg class="contact__icon" viewBox="0 0 10 10"><circle cx="5" cy="5" r="4.5"/><path d="M0.6 5 H9.4 M5 0.6 Q2.5 5 5 9.4 M5 0.6 Q7.5 5 5 9.4" fill="none" stroke="#fff" stroke-width="0.7"/></svg>
          www.steadyledgercoaching.com
        </li>
      </ul>
    </div>
  </section>

  <section class="card card--back">
    <div class="brand-lockup"><span class="brand-lockup__dot"></span>CLEARPATH MONEY COACHING</div>
    <h2 class="pitch__title">STRUGGLING WITH YOUR FINANCES?</h2>
    <ul class="pitch__list">
      <li>Learn to become debt free</li>
      <li>Discover the power of cash</li>
      <li>Control your money instead of it controlling you</li>
    </ul>
    <p class="pitch__promise">Let us help you achieve a new level of financial freedom!</p>
    <p class="offer"><span class="offer__label">SPECIAL OFFER!:</span> FREE 30 MINUTE CONSULTATION</p>
  </section>
</body>
</html>
```